4th Generation Family Business Needs a New Card Design!

We are a family owned 4th Generation company. We are based in the Sydney, Australia area and we are desperately in need of a more modern and classy card. We are monumental masons who design, supply & erect lasting memorials throughout cemeteries in Sydney. Our customers are normally in a period of grieving. I have attached logo files that will need to be implemented on the card. Company was established 1935. Australian Owned and Operated. Card needs to be designed to PIXO.com specification.

Target Market(s)

Our target market is based upon people that a grieving for family members that have passed away. We also deal with alot of companies that own and operate cemeteries.

Industry/Entity Type

Business

Contact Information for Business Card

Simon Harcourt, Operations Manager, 0417293086, simon@harcourtmemorials.com.au
Lewis Harcourt, Director, 0491630572, lewis@harcourtmemorials.com.au
Phone # 02 9561 3048
Website: www.harcourtmemorials.com.au
Address: Suite 17, 8 Palfrey Lane, West Carlow, Sydney NSW 2156

Font styles to use
Serif
Decorative
Script

Requirements
Must have
• Would like to see the logo nicely implemented with a modern design. Embossed lettering would be a nice additive.

```html
<!DOCTYPE html>
<html lang="en">
<head>
<meta charset="utf-8">
<title>Harcourt Memorials – Business Card</title>
<link href="https://fonts.googleapis.com/css2?family=Cinzel:wght@400;600&family=Open+Sans:wght@400&display=swap" rel="stylesheet">
<style>
  :root {
    --page-bg: #d9d9d9;
    --card-bg: #f1f1f3;
    --ink: #1c1c1c;
    --gold: #d4a72c;
    --body-text: #4a4a4a;
  }
  * { margin: 0; padding: 0; box-sizing: border-box; }
  html, body {
    width: 1105px;
    height: 1200px;
    overflow: hidden;
    background: var(--page-bg);
  }
  .card {
    position: absolute;
    left: 182px;
    width: 746px;
    height: 427px;
    background: var(--card-bg);
  }
  .card--front { top: 119px; }
  .card--back { top: 635px; }

  .accent-bar {
    position: absolute;
    left: 0;
    top: 55px;
    width: 15px;
    height: 54px;
    background: var(--gold);
  }
  .holder {
    position: absolute;
    left: 52px;
    top: 52px;
    font-family: "Cinzel", serif;
  }
  .holder__name {
    font-size: 28px;
    font-weight: 600;
    color: var(--ink);
    letter-spacing: 0.5px;
    line-height: 32px;
  }
  .holder__title {
    font-size: 20px;
    font-weight: 400;
    color: var(--gold);
    letter-spacing: 1px;
    line-height: 24px;
  }

  .brand-name {
    font-family: "Cinzel", serif;
    font-weight: 600;
    color: var(--ink);
    text-align: center;
    line-height: 1.1;
  }
  .card--front .brand-name {
    position: absolute;
    left: 40px;
    top: 240px;
    width: 270px;
    font-size: 34px;
  }
  .card--back .brand-name {
    position: absolute;
    left: 0;
    right: 0;
    top: 140px;
    font-size: 62px;
  }

  .contact {
    position: absolute;
    left: 391px;
    top: 200px;
    font-family: "Open Sans", sans-serif;
    font-size: 18.5px;
    color: var(--body-text);
    line-height: 28px;
  }
  .contact__address { margin-bottom: 12px; }
  .contact__list { list-style: none; }
  .contact__item {
    display: flex;
    align-items: center;
    height: 28px;
  }
  .contact__icon {
    width: 16px;
    height: 16px;
    margin-right: 13px;
    flex: none;
    fill: var(--ink);
  }
</style>
</head>
<body>
  <section class="card card--front">
    <div class="accent-bar"></div>
    <div class="holder">
      <p class="holder__name">Simon Harcourt</p>
      <p class="holder__title">Operations Manager</p>
    </div>

    <p class="brand-name">Harcourt<br>Memorials</p>

    <div class="contact">
      <p class="contact__address">Suite 17, 8 Palfrey Lane<br>West Carlow, Sydney NSW 2156</p>
      <ul class="contact__list">
        <li class="contact__item">
          <svg class="contact__icon" viewBox="0 0 16 16" aria-hidden="true"><path d="M3.5 1l2.5 3-1.5 2c1 2 3 4 5 5l2-1.5 3 2.5-1.5 2.5C8 15 1 8 1 2.5z"/></svg>
          02 9561 3048
        </li>
        <li class="contact__item">
          <svg class="contact__icon" viewBox="0 0 16 16" aria-hidden="true"><path d="M4 0h8a1 1 0 0 1 1 1v14a1 1 0 0 1-1 1H4a1 1 0 0 1-1-1V1a1 1 0 0 1 1-1zm1 2v10h6V2zm3 11a1 1 0 1 0 0 2 1 1 0 0 0 0-2z"/></svg>
          0417293086
        </li>
        <li class="contact__item">
          <svg class="contact__icon" viewBox="0 0 16 16" aria-hidden="true"><path d="M1 3h14v10H1zm1.5 1.2V5l5.5 4 5.5-4v-.8z"/></svg>
          simon@harcourtmemorials.com.au
        </li>
        <li class="contact__item">
          <svg class="contact__icon" viewBox="0 0 16 16" aria-hidden="true"><circle cx="8" cy="8" r="7.5"/><path d="M5 4c2 0 2 2 4 2s0 3-2 3-1 3-3 2S3 4 5 4zm6 5c1 0 2 1 1 3s-2 0-2-1 0-2 1-2z" fill="#f1f1f3"/></svg>
          www.harcourtmemorials.com.au
        </li>
      </ul>
    </div>
  </section>

  <section class="card card--back">
    <p class="brand-name">Harcourt Memorials</p>
  </section>
</body>
</html>
```